Tolvik Commercial Cleaning is lookong for a new business card design.

A fresh new design that's professional and stylish. We need a serious upgrade to our business cards. I have included pictures of our existing ones. Our clients include professional individuals and business owners. We woupdblike something professional and upbeat. Please have fun and see what you come uo with.

Target Market(s)

Property managers, business owners, facility managers and other similar professionals

Industry/Entity Type

Janitorial

Contact Information for Business Card

Name, cell, office number, email, web address

Font styles to use
Sans Serif

Colors

Designer to choose colors to be used in the design.

Requirements
Must have
• please use the green color in our logo
Nice to have
• Bar code
Should not have
• Address

```html
<!DOCTYPE html>
<html lang="en">
<head>
<meta charset="utf-8">
<title>Tolvik Commercial Cleaning – Business Card</title>
<link rel="stylesheet" href="https://fonts.googleapis.com/css2?family=Montserrat:wght@400;500;600;700&display=swap">
<style>
  :root {
    --page-bg: #e6e6e6;
    --brand-blue-dark: #2c5c92;
    --brand-blue-light: #4a7cad;
    --brand-navy: #2a5a90;
    --brand-green: #2ea44f;
    --card-white-a: #e3e3e3;
    --card-white-b: #f5f5f5;
    --text-grey: #5b5b5b;
    --white: #f4f3f1;
  }
  * { box-sizing: border-box; margin: 0; padding: 0; }
  html, body {
    width: 1200px; height: 1200px; overflow: hidden;
    background: var(--page-bg);
    font-family: "Montserrat", Arial, sans-serif;
  }
  .card {
    position: absolute;
    left: 235px;
    width: 730px;
    height: 417px;
  }
  .card--front {
    top: 160px;
    background: linear-gradient(135deg, var(--brand-blue-dark), var(--brand-blue-light));
    color: var(--white);
    text-align: center;
  }
  .card--back {
    top: 632px;
    background: linear-gradient(135deg, var(--card-white-a), var(--card-white-b));
  }
  .wordmark {
    position: absolute;
    left: 0; right: 0;
    font-weight: 600;
    letter-spacing: -2px;
    line-height: 1;
    text-align: center;
  }
  .card--front .wordmark { top: 122px; font-size: 112px; color: var(--white); }
  .card--back .wordmark { top: 58px; font-size: 100px; color: var(--brand-green); }
  .descriptor {
    position: absolute; left: 0; right: 0; top: 264px;
    font-size: 22px; font-weight: 500; letter-spacing: 0.5px;
  }
  .tagline {
    position: absolute; left: 0; right: 0; top: 360px;
    font-size: 19px; font-weight: 400; letter-spacing: 0.6px;
  }
  .person-name {
    position: absolute; left: 62px; top: 282px;
    font-size: 31px; font-weight: 700; color: var(--brand-navy);
    letter-spacing: -0.3px;
  }
  .contact {
    position: absolute; left: 391px; top: 240px;
    list-style: none;
  }
  .contact__company {
    font-size: 19px; font-weight: 700; color: var(--brand-green);
    margin-bottom: 6px;
  }
  .contact__item {
    display: flex; align-items: center; gap: 9px;
    font-size: 19px; color: var(--text-grey);
    height: 28px;
  }
  .contact__icon { width: 16px; height: 16px; fill: var(--brand-navy); flex: none; }
</style>
</head>
<body>
  <section class="card card--front">
    <div class="wordmark">tolvik</div>
    <div class="descriptor">commercial cleaning</div>
    <div class="tagline">better because we care</div>
  </section>

  <section class="card card--back">
    <div class="wordmark">tolvik</div>
    <div class="person-name">Marco Delgado</div>
    <ul class="contact">
      <li class="contact__company">Tolvik Commercial Cleaning</li>
      <li class="contact__item">
        <svg class="contact__icon" viewBox="0 0 24 24" aria-hidden="true"><path d="M6.6 10.8a15.1 15.1 0 0 0 6.6 6.6l2.2-2.2a1 1 0 0 1 1-.25 11.4 11.4 0 0 0 3.6.57 1 1 0 0 1 1 1V20a1 1 0 0 1-1 1A17 17 0 0 1 3 4a1 1 0 0 1 1-1h3.5a1 1 0 0 1 1 1c0 1.25.2 2.45.57 3.57a1 1 0 0 1-.25 1z"/></svg>
        (555) 014-2287
      </li>
      <li class="contact__item">
        <svg class="contact__icon" viewBox="0 0 24 24" aria-hidden="true"><path d="M2 5h20v14H2z M3.5 6.5 12 13l8.5-6.5" fill="var(--brand-navy)"/><path d="M3.5 6.5 12 13l8.5-6.5" fill="none" stroke="#fff" stroke-width="1.6"/></svg>
        marco@tolvikcleaning.com
      </li>
      <li class="contact__item">
        <svg class="contact__icon" viewBox="0 0 24 24" aria-hidden="true"><circle cx="12" cy="12" r="10"/><path d="M2 12h20M12 2c3 3 3 17 0 20M12 2c-3 3-3 17 0 20" fill="none" stroke="#fff" stroke-width="1.5"/></svg>
        www.tolvikcleaning.com
      </li>
    </ul>
  </section>
</body>
</html>
```